Request for Web Design Services – Lantern Trail

We are excited to announce a new project and are seeking talented web designers to create a visually stunning and intuitive website for our upcoming service, "Lantern Trail." This platform is dedicated to assisting foreign visitors in planning their journeys across Japan by highlighting the nation's beautiful shrines and temples. Please refer to the attached document for detailed design requirements.

Project Overview:
-Site Name: Lantern Trail
-Target Audience: Visitors to Japan
-Usage Scenario: Trip planning before and during the visit to Japan

Functionalities:
-Plotting the names and locations of shrines and temples across Japan
-Enabling users to select multiple shrines and temples and proposing optimal touring routes
-Intuitive user interface without relying heavily on language explanations

Deliverables:
-Source code (HTML, CSS, JavaScript, etc.)
-Site name logo
-Icons
-Favicon

Deadline:May 1, 2024

Design Requirements:
-Responsive design for both PC and mobile devices

Design Preferences:
-Catchy design suitable for coverage in domestic and international news media
-Unique design not typically created by Japanese designers
-Incorporation of Japanese traditions while maintaining a modern aesthetic
-Inclusion of motifs representing shrines and temples, such as bells and omikuji

We look forward to receiving your creative proposals and collaborating on this exciting project.

Best regards

Target Market(s)

Visitors to Japan

Industry/Entity Type

Information Technology

Coding

Coded - Design and coding required

Number of Pages Required

3 page

```html
<!DOCTYPE html>
<html lang="en">
<head>
<meta charset="utf-8">
<title>Lantern Trail – Shrine &amp; Temple Map</title>
<link rel="stylesheet" href="https://fonts.googleapis.com/css2?family=Noto+Sans:wght@400;500;600;700&family=Noto+Serif:wght@400&display=swap">
<style>
  :root {
    --ink: #111111;
    --white: #ffffff;
    --accent: #1ab3e8;
    --accent-soft: #d4eef8;
    --sea: #8ccfe2;
    --land: #a8dcc0;
    --land-deep: #93d1b0;
    --omikuji: #e6b94c;
    --omikuji-dark: #5b3a12;
    --pin: #e5152c;
    --shadow: 0 2px 8px rgba(0,0,0,0.18);
  }
  * { box-sizing: border-box; margin: 0; padding: 0; }
  html, body { width: 1200px; height: 738px; overflow: hidden; background: var(--white); }
  body { font-family: "Noto Sans", sans-serif; color: var(--ink); position: relative; }

  .site-header .menu-toggle { position: absolute; left: 60px; top: 26px; width: 34px; height: 24px; }
  .menu-toggle span { position: absolute; left: 0; width: 34px; height: 3px; background: var(--ink); border-radius: 2px; }
  .menu-toggle span:nth-child(1) { top: 0; }
  .menu-toggle span:nth-child(2) { top: 11px; }
  .menu-toggle span:nth-child(3) { top: 22px; }
  .site-title { position: absolute; left: 119px; top: 14px; font-size: 30px; font-weight: 600; letter-spacing: 0.3px; }
  .area-search { position: absolute; left: 935px; top: 16px; width: 203px; height: 45px; border: 1px solid var(--ink); border-radius: 23px; display: flex; align-items: center; padding-left: 32px; font-size: 15px; gap: 14px; }

  .map-view { position: absolute; left: 29px; top: 78px; width: 1142px; height: 619px; border-radius: 31px; overflow: hidden;
    background:
      radial-gradient(ellipse 160px 140px at 20px 0px, var(--sea) 95%, transparent 100%),
      radial-gradient(ellipse 260px 420px at 1180px 320px, var(--sea) 95%, transparent 100%),
      radial-gradient(ellipse 300px 120px at 900px 640px, var(--sea) 95%, transparent 100%),
      radial-gradient(ellipse 180px 60px at 800px 40px, var(--land-deep) 90%, transparent 100%),
      linear-gradient(135deg, var(--land-deep), var(--land) 55%, #b8e0cc); }

  .panel { position: absolute; background: var(--white); box-shadow: var(--shadow); }
  .planning-button { left: 71px; top: 140px; width: 174px; height: 38px; border-radius: 4px; display: flex; align-items: center; justify-content: space-between; padding: 0 14px 0 15px; font-size: 14px; font-weight: 600; }
  .site-list { left: 71px; top: 196px; width: 174px; height: 257px; border-radius: 4px; padding: 20px 0 0 16px; }
  .site-list h2 { font-size: 15px; font-weight: 600; margin-bottom: 12px; }
  .site-list li { list-style: none; display: flex; align-items: center; gap: 8px; height: 40px; font-size: 12px; }
  .site-list svg { width: 19px; height: 28px; margin-left: 1px; }

  .view-switch { left: 941px; top: 106px; width: 155px; height: 56px; border-radius: 3px; display: flex; align-items: center; padding-left: 25px; gap: 20px; }
  .toggle { width: 52px; height: 28px; border-radius: 14px; background: var(--accent); position: relative; }
  .toggle::after { content: ""; position: absolute; right: 3px; top: 3px; width: 22px; height: 22px; border-radius: 50%; background: var(--white); }

  .zoom-button { position: absolute; left: 1080px; width: 37px; height: 38px; background: var(--white); box-shadow: var(--shadow); display: flex; align-items: center; justify-content: center; }
  .zoom-in { top: 502px; }
  .zoom-out { top: 552px; }

  .sort-bar { left: 264px; top: 642px; width: 656px; height: 32px; border-radius: 16px; }
  .sort-select { position: absolute; left: 23px; top: 5px; font-size: 14px; display: flex; align-items: center; gap: 8px; }
  .track { position: absolute; top: 14px; height: 3px; border-radius: 2px; background: var(--accent-soft); }
  .track.active { background: var(--accent); height: 4px; }
  .step { position: absolute; top: 5px; font-family: "Noto Serif", serif; font-size: 13px; }

  .marker { position: absolute; width: 54px; height: 54px; margin: -27px 0 0 -27px; border-radius: 50%; background: var(--white); box-shadow: var(--shadow); display: flex; align-items: center; justify-content: center; }
  .marker svg { width: 17px; height: 26px; }
  .tour-360 { position: absolute; width: 40px; height: 32px; margin: -16px 0 0 -20px; }
</style>
</head>
<body>
<svg width="0" height="0" style="position:absolute">
  <defs>
    <symbol id="omikuji" viewBox="0 0 20 30">
      <path d="M2 5 L10 2 L18 5 L18 26 L10 29 L2 26 Z" fill="var(--omikuji)" stroke="var(--omikuji-dark)" stroke-width="1.4" stroke-linejoin="round"/>
      <path d="M2 5 L10 8 L18 5" fill="none" stroke="var(--omikuji-dark)" stroke-width="1.2"/>
      <path d="M10 8 V29" stroke="#f3d58c" stroke-width="1"/>
      <path d="M6 12 v10 M14 12 v10" stroke="var(--omikuji-dark)" stroke-width="0.8" stroke-dasharray="1.5 1.5"/>
    </symbol>
    <symbol id="tour360" viewBox="0 0 40 32">
      <text x="20" y="13" text-anchor="middle" font-family="Noto Sans, sans-serif" font-size="12" font-weight="600" fill="currentColor">360</text>
      <circle cx="33" cy="3" r="1.6" fill="none" stroke="currentColor" stroke-width="1"/>
      <path d="M7 12 C2 14 2 20 8 22 C14 24 26 24 32 22 C38 20 38 14 33 12" fill="none" stroke="currentColor" stroke-width="1.6"/>
      <path d="M5 17 C5 23 14 27 24 26" fill="none" stroke="currentColor" stroke-width="1.6"/>
      <path d="M21 23 L25 26 L21 29" fill="none" stroke="currentColor" stroke-width="1.6"/>
    </symbol>
  </defs>
</svg>

<header class="site-header">
  <div class="menu-toggle" aria-label="Menu"><span></span><span></span><span></span></div>
  <h1 class="site-title">Lantern Trail</h1>
  <div class="area-search">
    <svg width="24" height="24" viewBox="0 0 24 24" fill="none" stroke="var(--ink)" stroke-width="1.6"><circle cx="10" cy="10" r="8.5"/><path d="M16.5 16.5 L23 23"/></svg>
    <span>Search Area</span>
  </div>
</header>

<main>
  <div class="map-view" role="img" aria-label="Map of central Japan from Kyoto to Tokyo showing prefectures, cities and coastline"></div>

  <div class="panel planning-button">Planning
    <svg width="7" height="10" viewBox="0 0 7 10"><path d="M0 0 L7 5 L0 10 Z" fill="var(--ink)"/></svg>
  </div>

  <aside class="panel site-list">
    <h2>Shrines and Temples</h2>
    <ul>
      <li><svg><use href="#omikuji"/></svg>Lorem ipsum</li>
      <li><svg><use href="#omikuji"/></svg>Lorem ipsum</li>
      <li><svg><use href="#omikuji"/></svg>Lorem ipsum</li>
      <li><svg><use href="#omikuji"/></svg>Lorem ipsum</li>
      <li><svg><use href="#omikuji"/></svg>Lorem ipsum</li>
    </ul>
  </aside>

  <div class="panel view-switch">
    <svg width="40" height="32" style="color:var(--accent)"><use href="#tour360"/></svg>
    <div class="toggle" aria-label="360 view on"></div>
  </div>

  <div class="marker" style="left:612px;top:187px"><svg><use href="#omikuji"/></svg></div>
  <div class="marker" style="left:393px;top:281px"><svg><use href="#omikuji"/></svg></div>
  <div class="marker" style="left:543px;top:349px"><svg><use href="#omikuji"/></svg></div>
  <div class="marker" style="left:693px;top:406px"><svg><use href="#omikuji"/></svg></div>
  <div class="marker" style="left:362px;top:437px"><svg><use href="#omikuji"/></svg></div>
  <div class="marker" style="left:599px;top:481px"><svg><use href="#omikuji"/></svg></div>
  <div class="marker" style="left:474px;top:512px"><svg><use href="#omikuji"/></svg></div>
  <div class="marker" style="left:674px;top:281px">
    <svg viewBox="0 0 20 26" style="width:22px;height:29px"><path d="M10 1 C4.5 1 1 5 1 9.5 C1 16 10 25 10 25 C10 25 19 16 19 9.5 C19 5 15.5 1 10 1 Z" fill="var(--pin)"/><circle cx="10" cy="9.5" r="3.6" fill="var(--white)"/></svg>
  </div>

  <svg class="tour-360" style="left:661px;top:208px;color:var(--ink)"><use href="#tour360"/></svg>
  <svg class="tour-360" style="left:412px;top:409px;color:var(--ink)"><use href="#tour360"/></svg>
  <svg class="tour-360" style="left:548px;top:456px;color:var(--ink)"><use href="#tour360"/></svg>

  <div class="zoom-button zoom-in"><svg width="16" height="16" viewBox="0 0 16 16"><path d="M8 1 V15 M1 8 H15" stroke="var(--ink)" stroke-width="3"/></svg></div>
  <div class="zoom-button zoom-out"><svg width="16" height="16" viewBox="0 0 16 16"><path d="M1 8 H15" stroke="var(--ink)" stroke-width="3"/></svg></div>

  <div class="panel sort-bar">
    <div class="sort-select">Popular
      <svg width="9" height="6" viewBox="0 0 9 6"><path d="M0 0 H9 L4.5 6 Z" fill="var(--ink)"/></svg>
    </div>
    <div class="track" style="left:132px;width:115px"></div>
    <span class="step" style="left:253px">1</span>
    <div class="track active" style="left:267px;width:164px"></div>
    <span class="step" style="left:437px">2</span>
    <div class="track" style="left:451px;width:177px"></div>
  </div>
</main>
</body>
</html>
```